Modern Verdell Tree Care Website

I need a website for a full service Tree Care company. The company provides tree pruning, tree removal, tree preservation, emergency services, stump grinding, and emergency tree services.

Target Market(s)

Customers that need tree services

Industry/Entity Type

Landscaping, Tree Services

Coding

Coded - Design and coding required

Number of Pages Required

5+ page

Font styles to use
Sans Serif

Requirements
Must have
• Good clean design that showcases the services the company provides.
Nice to have
• Services page; contact form, blog, home page, about page

```html
<!DOCTYPE html>
<html lang="en">
<head>
<meta charset="utf-8">
<title>Verdell Tree Care</title>
<link href="https://fonts.googleapis.com/css2?family=Poppins:wght@400;500;600;700&display=swap" rel="stylesheet">
<style>
:root{
  --green:#7cc242;
  --green-dark:#1f2a10;
  --ink:#111111;
  --muted:#5e6b72;
  --peach:#f7c47f;
  --tan:#c8905a;
  --white:#ffffff;
  --card-shadow:0 4px 14px rgba(0,0,0,.08);
}
*{margin:0;padding:0;box-sizing:border-box}
html,body{width:1200px;height:3502px;overflow:hidden;background:var(--white)}
body{font-family:'Poppins',sans-serif;color:var(--ink);position:relative}
.abs{position:absolute}
.center{left:0;width:1200px;text-align:center}
.btn{position:absolute;background:var(--green);color:var(--ink);font-weight:600;font-size:17px;border-radius:12px;display:flex;align-items:center;justify-content:center}

/* header */
.brand{left:83px;top:32px;display:flex;align-items:center;gap:10px}
.brand-mark{width:30px;height:30px;background:var(--green);border-radius:4px}
.brand-name{font-size:20px;font-weight:700;color:var(--ink);line-height:1.1}
.nav{top:38px;font-size:17px;color:var(--muted)}
.nav.active{color:var(--green);font-weight:600}

/* hero */
.hero{left:0;top:99px;width:1200px;height:547px;background:linear-gradient(180deg,#5a5a4a 0%,#3d4532 35%,#2a3822 70%,#1e2a18 100%)}
.hero-title{top:212px;font-size:52px;font-weight:600;color:var(--white);line-height:76px}
.hero-text{top:375px;left:270px;width:660px;text-align:center;color:var(--white);font-size:17.5px;line-height:25px}

/* section headings */
.sec-title{font-size:35px;font-weight:600}
.sec-text{left:270px;width:660px;text-align:center;color:var(--muted);font-size:17px;line-height:25px}

/* service cards */
.card{width:317px;height:350px;background:var(--white);border-radius:24px;box-shadow:var(--card-shadow)}
.card-photo{position:absolute;left:16px;top:17px;width:285px;height:250px;border-radius:14px}
.card-num{position:absolute;left:134px;top:243px;width:48px;height:48px;border-radius:50%;background:var(--green);border:3px solid var(--white);display:flex;align-items:center;justify-content:center;font-weight:500;font-size:16px}
.card-label{position:absolute;left:0;width:317px;top:308px;text-align:center;font-weight:600;font-size:17px}

/* about */
.about-photo{left:83px;top:1729px;width:459px;height:333px;border-radius:28px;background:linear-gradient(135deg,#6b7a4a,#3d4a2a 50%,#7a6250)}
.deco{background:var(--peach);opacity:.85;border-radius:14px}
.about-title{left:617px;top:1728px;font-size:35px;font-weight:600}
.about-text{left:617px;top:1794px;width:500px;color:var(--muted);font-size:17px;line-height:25px;text-align:justify}

/* testimonial */
.quote{left:180px;width:840px;top:2386px;text-align:center;font-size:18px;line-height:25px;color:var(--ink)}
.quote-name{top:2495px;font-size:13.5px;color:var(--tan)}

/* cta */
.cta{left:83px;top:2640px;width:1034px;height:332px;border-radius:32px;background:linear-gradient(180deg,#3a4a2c,#24321c 60%,#1a2614)}
.cta-title{top:2695px;font-size:34px;font-weight:600;color:var(--white)}
.cta-text{left:260px;width:680px;top:2760px;text-align:center;color:var(--white);font-size:17.5px;line-height:25px}

/* footer */
.footer{left:83px;top:3100px;width:1034px;height:331px;border:2px solid var(--ink);border-radius:36px}
.footer-brand{left:117px;top:3140px;display:flex;align-items:center;gap:16px}
.footer-brand .brand-mark{width:56px;height:56px;border-radius:6px}
.footer-brand .brand-name{font-size:36px}
.foot-note{left:117px;top:3228px;width:360px;font-size:14px;line-height:18px}
.email{left:117px;top:3290px;width:240px;height:40px;border:1px solid var(--ink);border-radius:20px;padding-left:10px;display:flex;align-items:center;font-size:14px;color:#9aa0a4}
.subscribe{left:375px;top:3290px;width:99px;height:40px;border:1px solid var(--ink);border-radius:20px;display:flex;align-items:center;justify-content:center;font-size:14px}
.fine{left:117px;top:3348px;width:360px;font-size:8.5px;line-height:11px}
.col-head{top:3158px;font-size:19px;font-weight:600}
.col-item{font-size:16px}
.soc-dot{display:inline-block;width:14px;height:14px;border-radius:50%;background:var(--ink);margin-right:14px;vertical-align:-2px}
.legal{top:3449px;font-size:14px}
.legal a{color:var(--ink)}
</style>
</head>
<body>

<!-- header -->
<div class="abs brand"><span class="brand-mark"></span><span class="brand-name">Verdell Tree Care</span></div>
<div class="abs nav active" style="left:340px">Home</div>
<div class="abs nav" style="left:440px">Service</div>
<div class="abs nav" style="left:551px">Consulting</div>
<div class="abs nav" style="left:691px">Portfolio</div>
<div class="abs nav" style="left:810px">About</div>
<div class="btn" style="left:987px;top:24px;width:130px;height:51px">Let’s Talk</div>

<!-- hero -->
<div class="abs hero" role="img" aria-label="Misty pine forest at sunset with mountains behind"></div>
<h1 class="abs center hero-title">Your Trusted Full-Service<br>Tree Care Experts</h1>
<p class="abs hero-text">From tree pruning and removal to preservation and emergency services, our dedicated team ensures the health and beauty of your trees. Experience professional and reliable tree care solutions tailored to your needs.</p>
<div class="btn" style="left:526px;top:485px;width:149px;height:51px">Get Started</div>

<!-- services -->
<h2 class="abs center sec-title" style="top:697px">Our Services</h2>
<p class="abs sec-text" style="top:763px">Lorem ipsum dolor sit amet, consectetur adipiscing elit. Quisque nec sodales sem, molestie rhoncus lorem. In vel enim feugiat lorem blandit venenatis.</p>

<div class="abs card" style="left:83px;top:862px"><div class="card-photo" role="img" aria-label="Tree canopy seen from below" style="background:linear-gradient(135deg,#9bc45a,#3f6b22 55%,#6e6a4a)"></div><div class="card-num">1</div><div class="card-label">Tree Pruning</div></div>
<div class="abs card" style="left:442px;top:862px"><div class="card-photo" role="img" aria-label="Chainsaw resting on a cut log" style="background:linear-gradient(135deg,#a3927a,#8a7a62 50%,#b0783c)"></div><div class="card-num">2</div><div class="card-label">Tree Removal</div></div>
<div class="abs card" style="left:800px;top:862px"><div class="card-photo" role="img" aria-label="Hands holding a young seedling" style="background:linear-gradient(135deg,#3a4a2a,#5a4a38 55%,#2e3a22)"></div><div class="card-num">3</div><div class="card-label">Tree Preservation</div></div>

<div class="abs card" style="left:83px;top:1253px"><div class="card-photo" role="img" aria-label="Path through a pine forest" style="background:linear-gradient(160deg,#7a8a4a,#4a5a2a 55%,#8a7a40)"></div><div class="card-num">4</div><div class="card-label">Emergency Services</div></div>
<div class="abs card" style="left:442px;top:1253px"><div class="card-photo" role="img" aria-label="Hand grinding with a stone mortar and pestle" style="background:linear-gradient(135deg,#2a2e2c,#6a6e6a 55%,#3a3a38)"></div><div class="card-num">5</div><div class="card-label">Stump Grinding</div></div>
<div class="abs card" style="left:800px;top:1253px"><div class="card-photo" role="img" aria-label="Arborist climbing a tall tree with ropes" style="background:linear-gradient(135deg,#c4c8cc,#9aa0a4 55%,#4a5040)"></div><div class="card-num">6</div><div class="card-label">Emergency Tree Services</div></div>

<!-- about -->
<div class="abs about-photo" role="img" aria-label="Several hands resting together on a tree trunk"></div>
<div class="abs deco" style="left:500px;top:1771px;width:83px;height:83px"></div>
<div class="abs deco" style="left:117px;top:2041px;width:125px;height:41px"></div>
<h2 class="abs about-title">What Is Verdell Tree Care</h2>
<p class="abs about-text">Lorem ipsum dolor sit amet, consectetur adipiscing elit. Quisque nec sodales sem, molestie rhoncus lorem. In vel enim feugiat lorem blandit venenatis. Sed molestie ullamcorper facilisis. Morbi eu vehicula quam. Nunc et leo velit. Phasellus vitae interdum neque. Duis orci erat, vehicula a urna in, euismod facilisis neque. Etiam non interdum arcu, bibendum fermentum urna.</p>
<div class="btn" style="left:617px;top:2004px;width:147px;height:51px">Learn More</div>

<!-- testimonials -->
<h2 class="abs center sec-title" style="top:2188px">Testimonials</h2>
<p class="abs sec-text" style="top:2253px">Lorem ipsum dolor sit amet, consectetur adipiscing elit. Quisque nec sodales sem, molestie rhoncus lorem. In vel enim feugiat lorem blandit venenatis.</p>
<svg class="abs" style="left:90px;top:2412px" width="20" height="24" viewBox="0 0 20 24"><path d="M13 4 5 12l8 8" fill="none" stroke="#333" stroke-width="2.2"/></svg>
<svg class="abs" style="left:1090px;top:2412px" width="20" height="24" viewBox="0 0 20 24"><path d="m7 4 8 8-8 8" fill="none" stroke="#333" stroke-width="2.2"/></svg>
<p class="abs quote">Lorem ipsum dolor sit amet, consectetur adipiscing elit. Quisque nec sodales sem, molestie rhoncus lorem. In vel enim feugiat lorem blandit venenatis. Sed molestie ullamcorper facilisis. Morbi eu vehicula quam. Nunc et leo velit. Phasellus vitae interdum neque.</p>
<div class="abs center quote-name">-Marlon Reyes</div>

<!-- cta -->
<div class="abs cta" role="img" aria-label="Dark forest with tall tree trunks"></div>
<h2 class="abs center cta-title">Get a Free Estimate Today!</h2>
<p class="abs cta-text">Ready to enhance the beauty and safety of your property with expert tree care? Contact us now for a free, no-obligation estimate and discover the difference professional tree services can make.</p>
<div class="btn" style="left:472px;top:2870px;width:256px;height:49px">Request a Free Estimate</div>

<!-- footer -->
<div class="abs footer"></div>
<div class="abs footer-brand"><span class="brand-mark"></span><span class="brand-name">Verdell Tree Care</span></div>
<p class="abs foot-note">Stay up to date on the latest features by joining our newsletter.</p>
<div class="abs email">Enter your email</div>
<div class="abs subscribe">Subscribe</div>
<p class="abs fine">By subscribing, you agree to our Privacy Policy and consent to receive update from our company.</p>

<div class="abs col-head" style="left:542px">Verdell Tree</div>
<div class="abs col-item" style="left:542px;top:3203px">Services</div>
<div class="abs col-item" style="left:542px;top:3238px">Portfolio</div>
<div class="abs col-item" style="left:542px;top:3273px">Consulting</div>
<div class="abs col-item" style="left:542px;top:3308px">Let’s Talk</div>
<div class="abs col-item" style="left:542px;top:3343px">FAQ</div>

<div class="abs col-head" style="left:704px">About Us</div>
<div class="abs col-item" style="left:704px;top:3203px">Verdell Tree Care</div>
<div class="abs col-item" style="left:704px;top:3238px">Contact</div>
<div class="abs col-item" style="left:704px;top:3273px">Community</div>
<div class="abs col-item" style="left:704px;top:3308px">Maps</div>
<div class="abs col-item" style="left:704px;top:3343px">Verdell &amp; Business</div>

<div class="abs col-head" style="left:934px">Social Media</div>
<div class="abs col-item" style="left:934px;top:3203px"><span class="soc-dot"></span>Friendly</div>
<div class="abs col-item" style="left:934px;top:3238px"><span class="soc-dot"></span>Snapline</div>
<div class="abs col-item" style="left:934px;top:3273px"><span class="soc-dot"></span>Chirp</div>
<div class="abs col-item" style="left:934px;top:3308px"><span class="soc-dot"></span>Worknet</div>
<div class="abs col-item" style="left:934px;top:3343px"><span class="soc-dot"></span>Viewtube</div>

<div class="abs legal" style="left:83px">© 2024 Discover Verdell Tree Care, All right reserved.</div>
<div class="abs legal" style="left:723px"><a>Privacy Policy</a></div>
<div class="abs legal" style="left:852px"><a>Terms of Service</a></div>
<div class="abs legal" style="left:1000px"><a>Cookies Settings</a></div>

</body>
</html>
```